Design marketing/advertisement email for consulting business

Hello - My company, Brantor-Quisse, is looking for a marketing professional to compose a "marketing" email to be sent to potential professional referral sources. The email should provide an introduction of our company's capabilities and services. We want this marketing piece to invite the recipient to schedule a call with us to further discuss how we could best work together. The email must included elements of our brand. Our website is www.brantorquisse.example and will provide you with all the details about our business as well as our logo, branding, contact details etc. Thanks so much!
Updates
Industry/Entity Type
Business

```html
<!DOCTYPE html>
<html lang="en">
<head>
<meta charset="utf-8">
<title>Brantor-Quisse – Services Email</title>
<link href="https://fonts.googleapis.com/css2?family=Source+Sans+3:ital,wght@0,400;0,600;0,700;1,700&display=swap" rel="stylesheet">
<style>
  :root{
    --stage:#e6e7e8;
    --white:#ffffff;
    --ink:#2b2b2d;
    --charcoal:#3a3a3c;
    --slate:#6d6e71;
    --mist:#eceeed;
    --peach:#f7b28b;
    --peach-deep:#ee9262;
    --flame:#ee6a42;
    --flame-deep:#d9502c;
    --black-grad-top:#4a4a4c;
    --black-grad-bot:#111112;
  }
  *{box-sizing:border-box;margin:0;padding:0}
  html,body{width:1200px;height:559px;overflow:hidden;background:var(--stage)}
  body{font-family:"Source Sans 3",Arial,sans-serif;position:relative}

  .email{position:absolute;top:97px;width:508px;height:354px;background:var(--white);overflow:hidden;box-shadow:4px 5px 8px rgba(0,0,0,.35)}
  .email--photo{left:82px}
  .email--plain{left:640px}

  .hero-photo{position:absolute;left:193px;top:0;width:315px;height:354px;
    background:linear-gradient(160deg,#cfc8c2 0%,#b3aca8 35%,#8f8a88 60%,#d9d4cf 80%,#a69f98 100%)}

  .corner-block{position:absolute;left:430px;top:0;width:78px;height:88px;background:var(--charcoal)}
  .email--plain .corner-block{height:83px}

  .side-column{position:absolute;left:0;top:83px;width:193px;height:271px;background:var(--slate)}
  .email--photo .side-column{background:rgba(70,70,72,.72)}

  .copy-panel{position:absolute;left:193px;top:83px;width:237px;height:271px;background:var(--mist)}
  .email--photo .copy-panel{background:rgba(235,235,235,.42)}

  .brand{position:absolute;left:18px;top:20px;display:flex;align-items:center;gap:8px}
  .brand-square{width:30px;height:30px;background:var(--flame)}
  .brand-name{font-size:20px;font-weight:400;color:var(--ink);letter-spacing:.2px}

  .service-tab{position:absolute;left:0;width:192px;padding-left:13px;display:flex;flex-direction:column;justify-content:center;
    clip-path:polygon(0 0,160px 0,192px 50%,160px 100%,0 100%);color:var(--white)}
  .service-tab h2{font-size:13px;font-weight:700;text-transform:uppercase;line-height:1.1}
  .service-tab p{font-size:8.5px;margin-top:4px}
  .tab-development{top:84px;height:59px;background:linear-gradient(180deg,var(--black-grad-top),var(--black-grad-bot))}
  .tab-operation{top:163px;height:65px;background:linear-gradient(180deg,#fbd0b4,var(--peach) 55%,var(--peach-deep))}
  .tab-disposition{top:246px;height:65px;background:linear-gradient(180deg,#f58a66,var(--flame) 55%,var(--flame-deep))}
  .tab-operation h2,.tab-disposition h2{font-weight:600}

  .service-copy{position:absolute;left:198px;width:128px;color:var(--ink)}
  .service-copy h3{font-size:5.5px;font-weight:700}
  .service-copy p{font-size:5.5px;line-height:1.35}
  .copy-feasibility{top:105px}
  .copy-audits{top:171px}
  .copy-communications{top:256px}

  .contact-strip{position:absolute;left:288px;top:303px;width:220px;height:37px;background:rgba(255,255,255,.85);display:flex;align-items:center}
  .contact-label{font-size:14px;color:var(--ink);margin-left:0;width:88px}
  .contact-lines{font-size:7.5px;font-weight:700;font-style:italic;line-height:1.35;color:var(--ink)}
  .footer-bar{position:absolute;left:288px;top:340px;width:220px;height:14px;background:var(--charcoal)}
  .site-url{position:absolute;left:18px;top:333px;font-size:8px;color:var(--white)}
</style>
</head>
<body>

<section class="email email--photo">
  <div class="hero-photo" role="img" aria-label="Photo of a bright modern living room with a white sofa, framed art and a branch sculpture"></div>
  <div class="corner-block"></div>
  <div class="side-column"></div>
  <div class="copy-panel"></div>
  <div class="brand"><span class="brand-square"></span><span class="brand-name">Brantor-Quisse</span></div>
  <div class="service-tab tab-development"><h2>Development Services</h2><p>Acquisition, Planning and Design</p></div>
  <div class="service-tab tab-operation"><h2>Operation</h2><p>Audits and Assessments</p></div>
  <div class="service-tab tab-disposition"><h2>Disposition</h2><p>Transition and Exit Strategies</p></div>
  <div class="service-copy copy-feasibility"><h3>Feasibility Studies</h3><p>Site selection studies, demographic reports and mystery shopping of the local competition are services offered to ensure that you are building your community in the best location possible to maximize your investment.</p></div>
  <div class="service-copy copy-audits"><h3>Performance Audits</h3><p>Detailed on-site audits of the community and operator are offered, along with resident and staff satisfaction surveys. Additional services include analysis of the community's occupancy trends, financial performance, tour conversion rates and discounting strategies to provide you with a complete picture of the community's performance. These services can be provided on a quarterly or annual basis.</p></div>
  <div class="service-copy copy-communications"><h3>Community Communications</h3><p>Services include orchestrating the communication plan to announce the sale of the community to residents and staff, and working with the new operator to ensure that daily operations and key staff are maintained until the closing of the sale.</p></div>
  <div class="contact-strip"><span class="contact-label">Contact Us -</span><div class="contact-lines">PHONE: 555.010.4821<br>FAX: 555.010.7733<br>INFO@BRANTORQUISSE.EXAMPLE</div></div>
  <div class="footer-bar"></div>
  <div class="site-url">brantorquisse.example</div>
</section>

<section class="email email--plain">
  <div class="corner-block"></div>
  <div class="side-column"></div>
  <div class="copy-panel"></div>
  <div class="brand"><span class="brand-square"></span><span class="brand-name">Brantor-Quisse</span></div>
  <div class="service-tab tab-development"><h2>Development Services</h2><p>Acquisition, Planning and Design</p></div>
  <div class="service-tab tab-operation"><h2>Operation</h2><p>Audits and Assessments</p></div>
  <div class="service-tab tab-disposition"><h2>Disposition</h2><p>Transition and Exit Strategies</p></div>
  <div class="service-copy copy-feasibility"><h3>Feasibility Studies</h3><p>Site selection studies, demographic reports and mystery shopping of the local competition are services offered to ensure that you are building your community in the best location possible to maximize your investment.</p></div>
  <div class="service-copy copy-audits"><h3>Performance Audits</h3><p>Detailed on-site audits of the community and operator are offered, along with resident and staff satisfaction surveys. Additional services include analysis of the community's occupancy trends, financial performance, tour conversion rates and discounting strategies to provide you with a complete picture of the community's performance. These services can be provided on a quarterly or annual basis.</p></div>
  <div class="service-copy copy-communications"><h3>Community Communications</h3><p>Services include orchestrating the communication plan to announce the sale of the community to residents and staff, and working with the new operator to ensure that daily operations and key staff are maintained until the closing of the sale.</p></div>
  <div class="contact-strip"><span class="contact-label">Contact Us -</span><div class="contact-lines">PHONE: 555.010.4821<br>FAX: 555.010.7733<br>INFO@BRANTORQUISSE.EXAMPLE</div></div>
  <div class="footer-bar"></div>
  <div class="site-url">brantorquisse.example</div>
</section>

</body>
</html>
```